Namibia currently imports 60% of its food. Harvest Crest Oruva is an initiative which will assist Namibia to become self sustainable in terms of food production. We aim to do this through the development of 3 agricultural production zones which will include farming zones, local farmer assistance, processing and distribution of the final products. Please see our project overview attached.

```html
<!DOCTYPE html>
<html lang="en">
<head>
<meta charset="utf-8">
<title>Contact Us – Harvest Crest Oruva</title>
<link href="https://fonts.googleapis.com/css2?family=Merriweather:wght@400;700&family=Source+Serif+4:wght@400;600&display=swap" rel="stylesheet">
<style>
:root{
  --green:#0b6b3a;
  --tan:#c4a57f;
  --ink:#3a3a3a;
  --field:#ececec;
  --white:#ffffff;
}
*{margin:0;padding:0;box-sizing:border-box}
html,body{width:1200px;height:2289px;overflow:hidden;background:var(--white)}
body{position:relative;font-family:"Source Serif 4",Georgia,serif;color:var(--ink)}
.abs{position:absolute}
.brand{left:100px;top:58px;font-family:"Source Serif 4",Georgia,serif;font-weight:600;font-size:30px;color:var(--green);display:flex;align-items:center;gap:10px;white-space:nowrap}
.brand .dot{width:14px;height:14px;border-radius:50%;background:var(--green)}
.icon-circle{width:50px;height:50px;border-radius:50%;background:var(--green);display:flex;align-items:center;justify-content:center}
.contact-item{display:flex;gap:18px;align-items:flex-start}
.contact-item .label{font-family:"Merriweather",Georgia,serif;font-weight:700;font-size:15px;color:var(--green);line-height:1.2}
.contact-item .value{font-size:20px;color:var(--ink);margin-top:4px;margin-left:6px;white-space:nowrap}
.nav{top:112px;left:492px;display:flex;gap:27px;font-size:14px}
.nav a{color:var(--ink);text-decoration:none}
.nav a.active{color:var(--tan);position:relative}
.nav a.active::after{content:"";position:absolute;left:16px;right:10px;top:22px;height:2px;background:var(--tan)}
.hero{left:0;top:142px;width:1200px;height:518px;background:linear-gradient(100deg,#9fa899 0%,#6f8463 35%,#5d7a45 55%,#8a7560 80%,#a88e7c 100%)}
.hero-fade{left:0;top:142px;width:1200px;height:90px;background:linear-gradient(#fff,rgba(255,255,255,0))}
.hero-title{left:107px;top:358px;font-family:"Merriweather",Georgia,serif;font-weight:700;font-size:52px;color:var(--white)}
.play{left:768px;top:356px;width:58px;height:58px;border-radius:50%;background:var(--green);display:flex;align-items:center;justify-content:center;box-shadow:0 0 14px rgba(255,255,255,.6)}
.section-title{left:0;width:1200px;top:734px;text-align:center;font-family:"Merriweather",Georgia,serif;font-weight:700;font-size:46px;color:var(--green)}
.rule{left:551px;top:810px;width:98px;height:3px;background:var(--tan)}
.field-bg{left:0;top:1510px;width:1200px;height:358px;background:linear-gradient(#fff 0%,#8fb35a 18%,#5e8a2c 55%,#4f7a26 100%)}
.card{left:73px;top:1002px;width:1054px;height:659px;background:var(--white);border-radius:6px;box-shadow:0 0 6px rgba(11,107,58,.25)}
.card-photo{left:120px;top:1077px;width:439px;height:511px;border-radius:4px;background:linear-gradient(160deg,#c9c3b4 0%,#8a8f62 35%,#4f6b33 70%,#3c5526 100%)}
.form-label{font-size:13px;color:var(--ink)}
.field{background:var(--field)}
.submit{left:611px;top:1520px;width:154px;height:38px;background:var(--green);color:var(--white);font-size:17px;display:flex;align-items:center;justify-content:center;border-radius:2px}
.footer-brand{left:113px;top:2030px;font-family:"Source Serif 4",Georgia,serif;font-weight:600;font-size:34px;color:var(--green);display:flex;align-items:center;gap:12px;white-space:nowrap}
.footer-brand .dot{width:20px;height:20px;border-radius:50%;background:var(--green)}
.footer-col h3{font-family:"Merriweather",Georgia,serif;font-weight:700;font-size:22px;color:var(--green);margin-bottom:14px}
.footer-col li{list-style:none;font-size:18px;line-height:39px;color:var(--ink)}
.copy-line{top:2263px;height:1px;background:var(--tan);width:254px}
.copyright{left:0;width:1200px;top:2251px;text-align:center;font-size:15px}
</style>
</head>
<body>

<header>
  <div class="abs brand"><span class="dot"></span>Harvest Crest Oruva</div>

  <div class="abs contact-item" style="left:585px;top:27px">
    <div class="icon-circle"><svg width="22" height="22" viewBox="0 0 24 24"><path fill="#fff" d="M6.6 10.8a15 15 0 0 0 6.6 6.6l2.2-2.2c.3-.3.7-.4 1-.2 1.1.4 2.3.6 3.6.6.6 0 1 .4 1 1V20c0 .6-.4 1-1 1A17 17 0 0 1 3 4c0-.6.4-1 1-1h3.5c.6 0 1 .4 1 1 0 1.3.2 2.5.6 3.6.1.3 0 .7-.2 1z"/></svg></div>
    <div><div class="label">Call Us</div><div class="value">+ 1 555 010 2040</div></div>
  </div>
  <div class="abs contact-item" style="left:885px;top:27px">
    <div class="icon-circle"><svg width="22" height="22" viewBox="0 0 24 24"><path fill="#fff" d="M3 5h18v2l-9 6-9-6zm0 4l9 6 9-6v10H3z"/></svg></div>
    <div><div class="label">Email</div><div class="value">Info@HCOruva.org</div></div>
  </div>

  <nav class="abs nav">
    <a href="#">Home</a><a href="#">Food Security</a><a href="#">Farmer Empowerment &amp; Education</a><a href="#">Sustainability</a><a href="#" class="active">Contact Us</a>
  </nav>
</header>

<section>
  <div class="abs hero" role="img" aria-label="Smiling farmer carrying a crate of fresh vegetables in a greenhouse"></div>
  <div class="abs hero-fade"></div>
  <h1 class="abs hero-title">Contact Us</h1>
  <div class="abs play"><svg width="22" height="24" viewBox="0 0 22 24"><path fill="#fff" d="M3 2l17 10L3 22z"/></svg></div>
</section>

<section>
  <h2 class="abs section-title">Contact Us</h2>
  <div class="abs rule"></div>

  <div class="abs contact-item" style="left:114px;top:876px">
    <div class="icon-circle"><svg width="22" height="22" viewBox="0 0 24 24"><path fill="#fff" d="M6.6 10.8a15 15 0 0 0 6.6 6.6l2.2-2.2c.3-.3.7-.4 1-.2 1.1.4 2.3.6 3.6.6.6 0 1 .4 1 1V20c0 .6-.4 1-1 1A17 17 0 0 1 3 4c0-.6.4-1 1-1h3.5c.6 0 1 .4 1 1 0 1.3.2 2.5.6 3.6.1.3 0 .7-.2 1z"/></svg></div>
    <div><div class="label">Call Us</div><div class="value">+ 1 555 010 2040</div></div>
  </div>
  <div class="abs contact-item" style="left:417px;top:876px">
    <div class="icon-circle"><svg width="22" height="22" viewBox="0 0 24 24"><path fill="#fff" d="M3 5h18v2l-9 6-9-6zm0 4l9 6 9-6v10H3z"/></svg></div>
    <div><div class="label">Email</div><div class="value">Info@HCOruva.org</div></div>
  </div>
  <div class="abs contact-item" style="left:707px;top:876px">
    <div class="icon-circle"><svg width="22" height="22" viewBox="0 0 24 24"><path fill="#fff" d="M12 2a7 7 0 0 0-7 7c0 5 7 13 7 13s7-8 7-13a7 7 0 0 0-7-7zm0 9.5A2.5 2.5 0 1 1 12 6.5a2.5 2.5 0 0 1 0 5z"/></svg></div>
    <div><div class="label">Address</div><div class="value">45,Harvest Crest Oruva Na 500210.</div></div>
  </div>
</section>

<section>
  <div class="abs field-bg" role="img" aria-label="Rows of green crops stretching across a field"></div>
  <div class="abs card"></div>
  <div class="abs card-photo" role="img" aria-label="Smiling farmer holding a crate of carrots and greens in a field"></div>

  <form>
    <label class="abs form-label" style="left:610px;top:1101px">First Name</label>
    <div class="abs field" style="left:610px;top:1130px;width:229px;height:42px"></div>
    <label class="abs form-label" style="left:857px;top:1101px">Last Name</label>
    <div class="abs field" style="left:857px;top:1130px;width:229px;height:42px"></div>

    <label class="abs form-label" style="left:610px;top:1193px">Your Email</label>
    <div class="abs field" style="left:610px;top:1222px;width:229px;height:42px"></div>
    <label class="abs form-label" style="left:857px;top:1193px">Phone</label>
    <div class="abs field" style="left:857px;top:1222px;width:229px;height:42px"></div>

    <label class="abs form-label" style="left:610px;top:1284px">Your Message</label>
    <div class="abs field" style="left:610px;top:1312px;width:469px;height:180px"></div>

    <div class="abs submit">Submit</div>
  </form>
</section>

<footer>
  <div class="abs footer-brand"><span class="dot"></span>Harvest Crest Oruva</div>

  <div class="abs footer-col" style="left:538px;top:1950px">
    <h3>Quick Links</h3>
    <ul><li>Home</li><li>Food Security</li><li>Farmer Empowerment and Education</li><li>Sustainability</li><li>Contact Us</li></ul>
  </div>
  <div class="abs footer-col" style="left:919px;top:1952px">
    <h3>Other Links</h3>
    <ul><li>Terms and conditions</li><li>Privacy policy</li><li>Career</li><li>Help center</li><li>Support</li></ul>
  </div>

  <div class="abs copy-line" style="left:113px"></div>
  <div class="abs copy-line" style="left:834px"></div>
  <p class="abs copyright">Copyright © 2024 &nbsp;Harvest Crest Oruva. All rights reserved.</p>
</footer>

</body>
</html>
```